Design my dad a new business card because his current one sucks!

I need a business card designed for my fathers home maintenance business. His customers are individuals (single moms, old people etc.) as well as the occasional business. As such it needs to be accessible to both target audiences.

The front of the card should be dark grey on yellow with the logo and contain the following information:
- Darren Holtwick
- 0488 274 915
- info@brightoakhomecare.com.au
- 0488 274 915

- ABN: 71 284 630 912
- 'Fully Insured'

The reverse should be yellow on dark grey and will have the web address:
- brightoakhomecare.com.au

And a few key services he offers:
GENERAL REPAIRS
PAINTING/TILING/
PAVING &CONCRETING
PRESSURE WASHING
ON-SITE WELDING
DECKING ADDITIONS & REPAIRS
FENCING
FULL BOND CLEANING

This will be first time the logo has been printed so you will need to come up with the best CMYK approximation of the RGB colours to make sure it is a close as possible.

```html
<!DOCTYPE html>
<html lang="en">
<head>
<meta charset="utf-8">
<title>Bright Oak Home Care – Business Card</title>
<link rel="stylesheet" href="https://fonts.googleapis.com/css2?family=Michroma&family=Advent+Pro:wght@500&display=swap">
<style>
  :root {
    --page-bg: #ffffff;
    --card-yellow: #f7e600;
    --ink-grey: #4f4f4f;
  }
  * { margin: 0; padding: 0; box-sizing: border-box; }
  html, body {
    width: 1200px;
    height: 900px;
    overflow: hidden;
    background: var(--page-bg);
  }
  .canvas {
    position: relative;
    width: 1200px;
    height: 900px;
  }
  .business-card {
    position: absolute;
    left: 41px;
    top: 130px;
    width: 1119px;
    height: 620px;
    background: var(--card-yellow);
    color: var(--ink-grey);
  }
  .contact-name,
  .contact-phone {
    position: absolute;
    left: 67px;
    font-family: "Michroma", sans-serif;
    font-size: 38px;
    letter-spacing: 2px;
    line-height: 1;
    white-space: nowrap;
  }
  .contact-name { top: 86px; }
  .contact-phone { top: 140px; letter-spacing: 4px; }
  .contact-email {
    position: absolute;
    left: 67px;
    top: 200px;
    font-family: "Advent Pro", sans-serif;
    font-weight: 500;
    font-size: 40px;
    line-height: 1;
    white-space: nowrap;
  }
  .business-number,
  .insurance-note {
    position: absolute;
    left: 67px;
    font-family: "Advent Pro", sans-serif;
    font-weight: 500;
    font-size: 46px;
    line-height: 1;
    white-space: nowrap;
  }
  .business-number { top: 454px; }
  .insurance-note { top: 516px; }
  .brand-name {
    position: absolute;
    left: 1006px;
    top: 310px;
    transform: translate(-50%, -50%) rotate(-90deg);
    font-family: "Michroma", sans-serif;
    font-size: 30px;
    letter-spacing: 2px;
    line-height: 1;
    white-space: nowrap;
    color: var(--ink-grey);
  }
</style>
</head>
<body>
  <main class="canvas">
    <section class="business-card">
      <p class="contact-name">Darren Holtwick</p>
      <p class="contact-phone">0488 274 915</p>
      <p class="contact-email">info@brightoakhomecare.com.au</p>
      <p class="business-number">ABN: 71 284 630 912</p>
      <p class="insurance-note">'Fully Insured'</p>
      <p class="brand-name">BRIGHT OAK HOME CARE</p>
    </section>
  </main>
</body>
</html>
```